Animal Eye Clinic needs a Business card

We are a new veterinary ophthalmology practice (Ridgeline Pet Vision Care) and we need a business card designed. We only see animal eyes - we are not a regular veterinary clinic. We already have a logo. We are looking for a professional, good looking business card to hand out to our clients. We are looking for something simple but professional and contemporary. Our logo is likely the only picture/graphic that needs to be on the card.
Updates

Contact Information for Business Card

Delia Vossman, BSc, DVM, MSc, DipACVO
Veterinary Ophthalmologist

Phone: 250.418.3927
Email: ridgelinepetvisioncare@mailbox-example.net
Website: ridgelinepetvisioncare-example.net
Address: 1874 Thornbury Rd
Kelowna, BC, V1X 4M9

Colors

Designer to choose colors to be used in the design.

Requirements
Must have
• Our logo (attached)

```html
<!DOCTYPE html>
<html lang="en">
<head>
<meta charset="utf-8">
<title>Ridgeline Pet Vision Care – Business Card</title>
<link href="https://fonts.googleapis.com/css2?family=Arimo:wght@400;700&display=swap" rel="stylesheet">
<style>
  :root {
    --teal: #129aa7;
    --teal-dark: #0f8793;
    --grey: #7d7d7d;
    --grey-mid: #8a8a8a;
    --ink: #555555;
    --paper: #ffffff;
    --stage: #2a2a2a;
  }
  * { box-sizing: border-box; margin: 0; padding: 0; }
  html, body { width: 1200px; height: 880px; overflow: hidden; }
  body {
    background: var(--stage);
    font-family: "Arimo", Arial, sans-serif;
    position: relative;
  }
  .card {
    position: absolute;
    width: 560px;
    height: 320px;
    border-radius: 18px;
    overflow: hidden;
    box-shadow: 0 12px 30px rgba(0,0,0,.45);
  }

  /* Front */
  .card--front {
    left: 70px; top: 90px;
    background: linear-gradient(150deg, var(--teal) 0%, #3b9aa2 30%, #8a8f90 70%, var(--grey) 100%);
  }
  .brand {
    position: absolute;
    display: flex;
    align-items: center;
    gap: 14px;
  }
  .brand__dot {
    width: 44px; height: 44px;
    border-radius: 50%;
    flex: none;
  }
  .brand__name {
    font-weight: 700;
    text-transform: uppercase;
    line-height: 1.1;
    letter-spacing: .5px;
  }
  .card--front .brand { left: 60px; top: 128px; }
  .card--front .brand__dot { background: var(--paper); }
  .card--front .brand__name { color: var(--paper); font-size: 26px; }

  /* Back */
  .card--back {
    left: 570px; top: 470px;
    background: var(--paper);
  }
  .back-band { position: absolute; left: 0; top: 0; }
  .card--back .brand { left: 36px; top: 52px; }
  .card--back .brand__dot { width: 36px; height: 36px; background: var(--paper); }
  .card--back .brand__name { color: var(--paper); font-size: 24px; }

  .address {
    position: absolute;
    right: 30px; top: 98px;
    text-align: right;
    color: var(--ink);
    font-size: 13px;
    line-height: 1.45;
  }
  .divider-top {
    position: absolute;
    left: 410px; right: 30px; top: 84px;
    height: 1px; background: #bdbdbd;
  }

  .person { position: absolute; left: 34px; top: 182px; right: 30px; }
  .person__line { display: flex; align-items: baseline; gap: 0; }
  .person__name { color: var(--teal); font-weight: 700; font-size: 19px; }
  .person__creds { color: var(--teal); font-size: 17px; white-space: nowrap; }
  .person__rule { flex: 1; height: 1px; background: #bdbdbd; margin-left: 10px; align-self: center; }
  .person__title { color: var(--ink); font-size: 14px; margin-top: 3px; }

  .contacts { position: absolute; left: 34px; top: 240px; list-style: none; }
  .contacts li {
    display: flex; align-items: center; gap: 8px;
    color: var(--ink); font-size: 13px; line-height: 22px;
  }
  .contacts svg { width: 13px; height: 13px; flex: none; }
</style>
</head>
<body>

<section class="card card--front" aria-label="Business card front">
  <div class="brand">
    <span class="brand__dot"></span>
    <span class="brand__name">Ridgeline<br>Pet Vision Care</span>
  </div>
</section>

<section class="card card--back" aria-label="Business card back">
  <svg class="back-band" width="560" height="160" viewBox="0 0 560 160" aria-hidden="true">
    <polygon points="0,0 400,0 330,150 0,150" fill="var(--teal)"/>
    <polygon points="0,150 330,150 326,158 0,158" fill="var(--grey-mid)"/>
  </svg>

  <div class="brand">
    <span class="brand__dot"></span>
    <span class="brand__name">Ridgeline<br>Pet Vision Care</span>
  </div>

  <div class="divider-top"></div>
  <address class="address" style="font-style:normal">1874 Thornbury Rd<br>Kelowna, BC, V1X 4M9</address>

  <div class="person">
    <div class="person__line">
      <span class="person__name">Delia Vossman</span><span class="person__creds">, BSc, DVM, MSc, DipACVO</span>
      <span class="person__rule"></span>
    </div>
    <p class="person__title">Veterinary Ophthalmologist</p>
  </div>

  <ul class="contacts">
    <li>
      <svg viewBox="0 0 14 14" aria-hidden="true"><rect x="3" y="1" width="8" height="12" rx="1.5" fill="none" stroke="var(--teal)" stroke-width="1.6"/></svg>
      250.418.3927
    </li>
    <li>
      <svg viewBox="0 0 14 14" aria-hidden="true"><rect x="1" y="3" width="12" height="8" fill="var(--teal)"/><polyline points="1,3 7,8 13,3" fill="none" stroke="#fff" stroke-width="1.2"/></svg>
      ridgelinepetvisioncare@mailbox-example.net
    </li>
    <li>
      <svg viewBox="0 0 14 14" aria-hidden="true"><circle cx="7" cy="7" r="6" fill="var(--teal)"/><ellipse cx="7" cy="7" rx="2.5" ry="6" fill="none" stroke="#fff" stroke-width=".9"/><line x1="1" y1="7" x2="13" y2="7" stroke="#fff" stroke-width=".9"/></svg>
      ridgelinepetvisioncare-example.net
    </li>
  </ul>
</section>

</body>
</html>
```